Adelaide based cleaning and remediation business needs a website design

We are launching a new company with no clients as yet so we don't have the benefit of Plimora Reviews to build confidence. We can use our  past work history with other employers in the industry to give some credibility. Happy to use any colour scheme as long as it look interesting when people click on the site it gets there attention. enquiry . I have supplied a mock up the important information and various photos as they tell a lot of the story.

```html
<!DOCTYPE html>
<html lang="en">
<head>
<meta charset="utf-8">
<title>Karsten Services</title>
<link href="https://fonts.googleapis.com/css2?family=Poppins:wght@400;500;600;700;800&display=swap" rel="stylesheet">
<style>
:root{
  --blue:#3a8ee6;
  --navy:#0d1628;
  --navy-soft:#2a3a58;
  --ink:#111111;
  --text:#444444;
  --grey-band:#f1f1f1;
  --white:#ffffff;
}
*{margin:0;padding:0;box-sizing:border-box}
html,body{width:1200px;height:4367px;overflow:hidden}
body{position:relative;background:var(--white);font-family:'Poppins',sans-serif;color:var(--ink)}
.abs{position:absolute}
.btn{position:absolute;display:flex;align-items:center;justify-content:center;gap:8px;border-radius:30px;color:var(--white);font-weight:600;font-size:13px;letter-spacing:.3px}
.btn-blue{background:var(--blue)}
.btn-navy{background:var(--navy)}
.btn .dot{width:12px;height:12px;border-radius:50%;background:var(--white);display:inline-flex;align-items:center;justify-content:center}
.btn .dot::after{content:"";border-left:5px solid var(--blue);border-top:3px solid transparent;border-bottom:3px solid transparent;margin-left:1px}
.btn-navy .dot::after{border-left-color:var(--navy)}
.photo{position:absolute}

/* top bar */
.topbar-mail{left:505px;top:0;width:335px;height:51px;background:var(--blue);clip-path:polygon(6% 0,100% 0,100% 100%,0 100%);display:flex;align-items:center;padding-left:60px;gap:14px;color:#fff;font-size:14px}
.topbar-call{left:827px;top:0;width:266px;height:51px;background:var(--navy);clip-path:polygon(0 0,100% 0,88% 100%,0 100%);display:flex;align-items:center;padding-left:24px;gap:14px;color:#fff;font-size:13px;font-weight:500}
.icon-circle{width:28px;height:28px;border-radius:50%;background:#fff;display:flex;align-items:center;justify-content:center}
.logo-box{left:97px;top:0;width:184px;height:195px;background:#fff;box-shadow:0 2px 6px rgba(0,0,0,.15);z-index:5;display:flex;flex-direction:column;align-items:center;justify-content:center;gap:10px}
.logo-box .brand-name{font-weight:700;font-size:16px;color:var(--navy)}
.logo-box .brand-mark{width:26px;height:26px;background:var(--blue)}
.nav{top:82px;left:363px;display:flex;gap:22px;font-size:14px;font-weight:600;color:var(--ink)}
.nav .active{color:var(--blue)}

/* hero */
.hero-photo{left:0;top:129px;width:1200px;height:680px;background:linear-gradient(120deg,#2c2622 0%,#4a3a30 30%,#3b4552 55%,#2f6fb8 75%,#1f2a3a 100%)}
.hero-circle{left:116px;top:238px;width:406px;height:406px;border-radius:50%;background:radial-gradient(circle at 50% 45%,#fff 60%,#e6e6e6 100%);border:6px solid #fff;box-shadow:0 6px 24px rgba(0,0,0,.35);text-align:center}
.hero-circle .welcome{margin-top:72px;font-size:22px;font-weight:600}
.hero-circle h1{margin-top:14px;font-size:58px;line-height:66px;font-weight:800;color:var(--ink)}
.hero-edge{left:0;top:620px}

/* section titles */
.section-title{position:absolute;left:0;width:1200px;text-align:center;font-size:48px;font-weight:700;line-height:1}
.section-title span{color:var(--blue)}
.title-rule{position:absolute;height:4px;width:88px;background:var(--navy);left:556px}

/* about */
.about-offset{left:105px;top:1110px;width:285px;height:319px;background:var(--blue)}
.about-photo{left:122px;top:912px;width:449px;height:502px;background:linear-gradient(160deg,#5a4a3e,#7a5a44 40%,#4e5e38 75%,#3d4a2c)}
.about-title{left:668px;top:938px;font-size:48px;font-weight:700}
.about-title span{color:var(--blue)}
.about-rule{left:668px;top:1000px;width:84px;height:4px;background:var(--navy)}
.about-copy{left:668px;top:1020px;width:416px;font-size:12.8px;line-height:25.7px;color:var(--text);text-align:justify}
.about-copy p+p{margin-top:18px}

/* services */
.service{position:absolute;border-radius:50%;display:flex;flex-direction:column;align-items:center;justify-content:center;text-align:center;color:#fff;border:8px solid #fff;box-shadow:0 4px 16px rgba(0,0,0,.2)}
.service-side{width:344px;height:344px;background:linear-gradient(160deg,#4a96e2,#2a78d0);font-size:21px;font-weight:700;line-height:30px}
.service-main{width:430px;height:430px;background:radial-gradient(circle at 50% 40%,#23324f,#0e1930);z-index:2;padding:0 38px}
.service-main h3{font-size:21px;font-weight:700;margin-bottom:22px}
.service-main p{font-size:14px;line-height:25px}
.service-main .more{margin-top:22px;width:26px;height:26px;border-radius:50%;background:#fff;display:flex;align-items:center;justify-content:center}
.service-main .more::after{content:"";border-left:8px solid var(--navy);border-top:5px solid transparent;border-bottom:5px solid transparent;margin-left:2px}

/* testimonials */
.testimonial-band{left:0;top:2200px;width:1200px;height:597px;background:var(--grey-band)}
.card{position:absolute;background:#fff;border-radius:6px;box-shadow:0 4px 14px rgba(0,0,0,.08);padding:20px 20px}
.card .head{display:flex;align-items:center;gap:14px}
.card .avatar{width:62px;height:62px;border-radius:50%;background:linear-gradient(135deg,#c9b8a6,#8c7a6a);flex:none}
.card .name{font-size:13px;font-weight:700;color:var(--ink)}
.card .role{font-size:11.5px;color:var(--blue);margin-top:4px}
.card .quote{margin-top:18px;font-size:11px;line-height:18px;color:#555}
.card-main .name{font-size:15px}
.card-main .role{font-size:13px}
.card-main .avatar{width:72px;height:72px}
.arrow{position:absolute;width:50px;height:50px;border-radius:50%;background:#fff;box-shadow:0 2px 8px rgba(0,0,0,.15);display:flex;align-items:center;justify-content:center;font-weight:700;font-size:20px}

/* gallery */
.tile{position:absolute}

/* footer */
.footer-bg{left:0;top:3760px}
.footer-ask{left:303px;top:3905px;color:#fff;font-size:14px;font-weight:600}
.footer-ask small{display:block;margin-top:14px;font-size:13px;font-weight:400}
.field{position:absolute;top:3995px;height:44px;background:#fff;border-radius:22px;font-size:13px;color:#222;padding-left:22px;display:flex;align-items:center}
.send{position:absolute;right:8px;top:8px;width:28px;height:28px;border-radius:50%;background:var(--blue)}
.cert-badge{left:112px;top:4088px;width:88px;height:88px;border-radius:50%;background:var(--navy-soft)}
.foot-col{position:absolute;top:4084px;color:#fff;font-size:11px;line-height:25px}
.foot-col h4{font-size:12.5px;font-weight:600;margin-bottom:10px}
.foot-rule{left:144px;top:4237px;width:915px;height:1px;background:#3a4560}
.copyright{left:0;top:4266px;width:1200px;text-align:center;color:#fff;font-size:13px}
</style>
</head>
<body>

<!-- Header -->
<div class="abs topbar-mail">
  <div class="icon-circle"><svg width="14" height="10" viewBox="0 0 14 10"><rect x="0.5" y="0.5" width="13" height="9" fill="none" stroke="#0d1628"/><path d="M1 1l6 5 6-5" fill="none" stroke="#0d1628"/></svg></div>
  admin@karstenservices.com
</div>
<div class="abs topbar-call">
  <div class="icon-circle"><svg width="13" height="13" viewBox="0 0 24 24"><path d="M6.6 10.8a15 15 0 006.6 6.6l2.2-2.2a1 1 0 011-.25 11 11 0 003.6.6 1 1 0 011 1V20a1 1 0 01-1 1A17 17 0 013 4a1 1 0 011-1h3.5a1 1 0 011 1 11 11 0 00.6 3.6 1 1 0 01-.25 1z" fill="#0d1628"/></svg></div>
  Call Us &nbsp;- &nbsp;0400 555 123
</div>
<div class="abs logo-box">
  <div class="brand-mark"></div>
  <div class="brand-name">Karsten Services</div>
</div>
<nav class="abs nav">
  <span class="active">HOME</span><span>ABOUT US</span><span>OUR SERVICES</span><span>TESTIMONIALS</span><span>CONTACT US</span>
</nav>
<div class="btn btn-navy" style="left:908px;top:69px;width:178px;height:48px;font-size:14px">GET A QUOTE <span class="dot"></span></div>

<!-- Hero -->
<div class="photo hero-photo" role="img" aria-label="Worker in blue protective suit and respirator clearing scrap metal debris"></div>
<svg class="abs hero-edge" width="1200" height="190" viewBox="0 0 1200 190">
  <polygon points="640,80 740,150 985,12 1200,130 1200,150 985,30 740,168 640,100" fill="#3a8ee6"/>
  <polygon points="0,160 460,148 640,86 740,160 985,22 1200,138 1200,190 0,190" fill="#0d1628"/>
  <polygon points="0,178 460,168 640,108 740,180 985,44 1200,158 1200,190 0,190" fill="#ffffff"/>
</svg>
<div class="abs hero-circle">
  <div class="welcome">WELCOME TO</div>
  <h1>KARSTEN<br>SERVICES</h1>
  <div class="btn btn-blue" style="left:107px;top:283px;width:178px;height:44px">GET A QUOTE <span class="dot"></span></div>
</div>

<!-- About -->
<div class="abs about-offset"></div>
<div class="photo about-photo" role="img" aria-label="Rusted scrap metal and an old bicycle piled in an overgrown yard"></div>
<h2 class="abs about-title">ABOUT <span>US</span></h2>
<div class="abs about-rule"></div>
<div class="abs about-copy">
  <p>Adelaide-based Karsten Services is a family-run organisation. We have been in operation for more than two decades. We've gained some knowledge about cleaning and squalor removal services throughout the years. As a small South Australian company, we base everything on responsibility honesty and fairness. We are aware of the confidence you put in us when you seek our help.</p>
  <p>Prices provided in terms of the number of hours and service required or as a fixed quotation according to the quantity of clutter, pigeon faeces, and mould disposal expenses, however, hoarding cleaning can be different as this may require sorting and can require more organisation.</p>
</div>
<div class="btn btn-blue" style="left:668px;top:1364px;width:178px;height:44px">VIEEW MORE <span class="dot"></span></div>

<!-- Services -->
<h2 class="section-title" style="top:1558px">OUR <span>SERVICES</span></h2>
<div class="title-rule" style="top:1617px"></div>
<div class="service service-side" style="left:103px;top:1701px" role="img" aria-label="Squalor estate clean up scene tinted blue">SQULAOR ESTATE<br>CLEAN UPS</div>
<div class="service service-side" style="left:755px;top:1701px" role="img" aria-label="Fire damaged room tinted blue">FIRE DAMAGE<br>CLEAN UPS</div>
<div class="service service-main" style="left:385px;top:1658px">
  <h3>PIGEON WASTE</h3>
  <p>Prices provided in terms of the number of hours and service required or as a fixed quotation according to the quantity of clutter, pigeon faeces, and mould disposal expenses, however, hoarding cleaning can be different as this may require sorting and can require more organisation.</p>
  <div class="more"></div>
</div>

<!-- Testimonials -->
<div class="abs testimonial-band"></div>
<h2 class="section-title" style="top:2299px">OUR <span>TESTIMONIALS</span></h2>
<div class="title-rule" style="top:2357px"></div>
<div class="arrow" style="left:34px;top:2483px">&laquo;</div>
<div class="arrow" style="left:1114px;top:2483px;color:#f2a21b">&raquo;</div>
<div class="card" style="left:114px;top:2415px;width:286px;height:227px">
  <div class="head"><div class="avatar" role="img" aria-label="Client portrait"></div><div><div class="name">TOBIN ELSWICK</div><div class="role">Satisfied Client in USA</div></div></div>
  <div class="quote">Engaged Karsten Services to clean bird poo from our commercial building facade. Job was so well done it exceeded our expectations.</div>
</div>
<div class="card card-main" style="left:434px;top:2395px;width:332px;height:266px">
  <div class="head"><div class="avatar" role="img" aria-label="Client portrait"></div><div><div class="name">NADIA VERHOEF</div><div class="role">Satisfied Client in USA</div></div></div>
  <div class="quote">Daniel and his team arrived the next morning to clean up a rental property my husband and I own which and had been trashed by the tenants. He was the only contractor to return my call They did an amazing job and also deodorised the house for no extra charge</div>
</div>
<div class="card" style="left:800px;top:2415px;width:286px;height:227px">
  <div class="head"><div class="avatar" role="img" aria-label="Client portrait"></div><div><div class="name">LENA MARCHETTI</div><div class="role">Satisfied Client in USA</div></div></div>
  <div class="quote">Excellent service. Very happy with outcome Did the job as quoted</div>
</div>

<!-- Gallery -->
<h2 class="section-title" style="top:2909px">OUR <span>GALLERY</span></h2>
<div class="title-rule" style="top:2967px"></div>
<div class="tile" style="left:115px;top:3005px;width:382px;height:373px;background:linear-gradient(150deg,#4b4638,#6b6248 50%,#3a3a30)" role="img" aria-label="Floor covered in scrap parts and boxes"></div>
<div class="tile" style="left:115px;top:3388px;width:382px;height:241px;background:linear-gradient(150deg,#5a3a30,#8a6a50 45%,#3a4a6a)" role="img" aria-label="Cluttered storage shelves full of hoarded items"></div>
<div class="tile" style="left:510px;top:3009px;width:314px;height:267px;background:linear-gradient(170deg,#c07a80,#4a3a32 45%,#2a2420)" role="img" aria-label="Fire damaged kitchen with exposed insulation"></div>
<div class="tile" style="left:510px;top:3290px;width:314px;height:341px;background:linear-gradient(160deg,#4a4a44,#6a5040 50%,#3a3832)" role="img" aria-label="Derelict room full of debris"></div>
<div class="tile" style="left:837px;top:3010px;width:248px;height:212px;background:linear-gradient(180deg,#dcdcd8,#c8c0a0 60%,#b0a880)" role="img" aria-label="Pigeons perched on a soiled ledge"></div>
<div class="tile" style="left:837px;top:3236px;width:248px;height:212px;background:linear-gradient(170deg,#7aa040,#505a60 50%,#2a2e30)" role="img" aria-label="Worker in protective suit cleaning a roof gutter"></div>
<div class="tile" style="left:837px;top:3460px;width:248px;height:171px;background:linear-gradient(160deg,#3a3c38,#5a5a50 50%,#2a2c2a)" role="img" aria-label="Bird droppings built up along a beam"></div>
<div class="btn btn-blue" style="left:510px;top:3665px;width:178px;height:44px">VIEW MORE <span class="dot"></span></div>

<!-- Footer -->
<svg class="abs footer-bg" width="1200" height="607" viewBox="0 0 1200 607">
  <polygon points="0,55 212,175 458,12 560,80 730,45 1200,10 1200,607 0,607" fill="#0d1628"/>
  <polyline points="40,70 212,150 458,0 560,62 740,30 1200,4" fill="none" stroke="#3a8ee6" stroke-width="10"/>
</svg>
<div class="abs footer-ask">Got more questions about our clean-up services and what we offer?<small>Get in touch today M 0400 555 123</small></div>
<div class="btn btn-blue" style="left:910px;top:3915px;width:176px;height:45px">GET IN TOUCH <span class="dot"></span></div>
<div class="field" style="left:115px;width:205px">Name</div>
<div class="field" style="left:329px;width:205px">Email</div>
<div class="field" style="left:542px;width:205px">Phone</div>
<div class="field" style="left:756px;width:325px">Message<span class="send"></span></div>

<div class="abs cert-badge" role="img" aria-label="Industry certification badge"></div>
<div class="foot-col" style="left:437px">
  <h4>CONTACT US</h4>
  14 Wexley Road Unley SA 5061<br>Call: Daniel or Priya 0400 555 123<br>Email: admin@karstenservices.com
</div>
<div class="foot-col" style="left:754px">
  <h4>BUSINESS HOURS</h4>
  Monday to Saturday<br>8:00 am to 4:00 pm
</div>
<div class="foot-col" style="left:995px">
  <h4>SOCIAL MEDIA</h4>
  Facepage<br>Snapgram
</div>
<div class="abs foot-rule"></div>
<div class="abs copyright">Copyright@2025.All Rights Reserved</div>

</body>
</html>
```